Tech Savy small Business accountant business card design

We need a business card for a new company based in the cloud. We provide tax, business advisory, accounting, information technology solutions and back office functions to small businesses. We offer fixed fee packages with add on services as you need them. By harnessing technology we simplify small business operational processes providing valuable time and information for small business owners to grow their business. In the logo (bluvoria) we want to be able to see bluv and experts. The final design should communicate achieving growth dreams and balance (ie life and $).
Updates
This project has been temporarily placed on hold until I finalize "Tech Savy small Business accountant needs a logo". I invite all designers to submit on this logo project. Once my logo is finalized I will resume this business card contest. Thanks Added Wednesday, March 19, 2014
This project has been temporarily placed on hold until I finalize "Tech Savy small Business accountant logo". I invite all designers to submit on this logo project. Once my logo is finalized I will resume this business card contest. Thanks Added Thursday, March 20, 2014
Target Market(s)
Small Business (Revenue $500,000, more than 3 employees) owners.
Industry/Entity Type
Small Business
Contact Information for Business Card
Marcy Elwind (Principal)
Accountant, Tax Agent.
TEL | 0417 683 912
EMAIL | Marcy.Elwind@bluvoria.com.au
WEB | www.bluvoria.com.au
Look and feel

```html
<!DOCTYPE html>
<html lang="en">
<head>
<meta charset="utf-8">
<title>bluvoria business card</title>
<link rel="stylesheet" href="https://fonts.googleapis.com/css2?family=Open+Sans:wght@400;600;700;800&display=swap">
<style>
  :root {
    --backdrop: #ecebe8;
    --blue-light: #5cc6ec;
    --blue-mid: #2a9ad8;
    --blue-deep: #1577c2;
    --white: #ffffff;
    --ink: #1b1b1b;
    --brand-blue: #1a86d0;
    --muted-white: rgba(255,255,255,0.85);
  }
  * { margin: 0; padding: 0; box-sizing: border-box; }
  html, body {
    width: 1200px; height: 913px; overflow: hidden;
    background: var(--backdrop);
    font-family: "Open Sans", Arial, sans-serif;
  }
  .stage {
    position: relative; width: 1200px; height: 913px;
    display: flex; align-items: center; justify-content: center; gap: 40px;
  }
  .card {
    position: relative; width: 520px; height: 297px;
    box-shadow: 0 6px 18px rgba(0,0,0,0.18);
  }
  .card--front {
    background: linear-gradient(160deg, var(--blue-light) 0%, var(--blue-mid) 50%, var(--blue-deep) 100%);
    color: var(--white);
  }
  .card--back { background: var(--white); }

  .person {
    position: absolute; top: 62px; left: 0; right: 0; text-align: center;
  }
  .person__name {
    font-weight: 700; font-size: 20px; letter-spacing: 0.5px; text-transform: uppercase;
  }
  .person__name span { text-transform: none; }
  .person__role {
    font-size: 13px; color: var(--muted-white); margin-top: 2px;
  }

  .front-brand {
    position: absolute; left: 38px; top: 160px;
  }
  .brand-name {
    font-weight: 800; letter-spacing: -1px; line-height: 1;
  }
  .front-brand .brand-name { font-size: 40px; color: var(--white); }
  .front-brand .tagline { font-size: 10.5px; font-weight: 600; margin-top: 3px; }

  .divider {
    position: absolute; left: 262px; top: 150px; width: 1px; height: 82px;
    background: var(--muted-white);
  }
  .contacts {
    position: absolute; left: 276px; top: 156px; list-style: none;
    font-size: 12.5px; line-height: 24px;
  }
  .contacts li { display: flex; align-items: center; gap: 8px; }
  .contacts svg { width: 12px; height: 12px; flex: none; }

  .back-brand {
    position: absolute; left: 0; right: 0; top: 100px; text-align: center;
  }
  .back-brand .brand-name { font-size: 66px; color: var(--brand-blue); }
  .back-brand .tagline {
    font-size: 15.5px; font-weight: 600; color: var(--ink); margin-top: 6px;
  }
</style>
</head>
<body>
<main class="stage">
  <section class="card card--front" aria-label="Business card front">
    <div class="person">
      <p class="person__name">Marcy Elwind <span>(Principal)</span></p>
      <p class="person__role">Accountant, Tax Agent</p>
    </div>
    <div class="front-brand">
      <p class="brand-name">bluvoria</p>
      <p class="tagline">Your business and accounting partner</p>
    </div>
    <div class="divider"></div>
    <ul class="contacts">
      <li>
        <svg viewBox="0 0 24 24" aria-hidden="true"><path fill="#fff" d="M6.6 10.8a15 15 0 0 0 6.6 6.6l2.2-2.2a1 1 0 0 1 1-.25 11.4 11.4 0 0 0 3.6.57 1 1 0 0 1 1 1V20a1 1 0 0 1-1 1A17 17 0 0 1 3 4a1 1 0 0 1 1-1h3.5a1 1 0 0 1 1 1c0 1.25.2 2.45.57 3.6a1 1 0 0 1-.25 1z"/></svg>
        0417 683 912
      </li>
      <li>
        <svg viewBox="0 0 24 24" aria-hidden="true"><g fill="none" stroke="#fff" stroke-width="2"><circle cx="12" cy="12" r="10"/><path d="M2 12h20M12 2c3 3 3 17 0 20M12 2c-3 3-3 17 0 20"/></g></svg>
        www.bluvoria.com.au
      </li>
      <li>
        <svg viewBox="0 0 24 24" aria-hidden="true"><g fill="none" stroke="#fff" stroke-width="2"><rect x="2" y="5" width="20" height="14"/><path d="M2 5l10 8 10-8"/></g></svg>
        Marcy.Elwind@bluvoria.com.au
      </li>
    </ul>
  </section>

  <section class="card card--back" aria-label="Business card back">
    <div class="back-brand">
      <p class="brand-name">bluvoria</p>
      <p class="tagline">Your business and accounting partner</p>
    </div>
  </section>
</main>
</body>
</html>
```